Finish Trifold + logo, Design and layout already done, need to be made visually appealing.

I already have the logo design, but need it polished and in the correct format for printing.
I started the tri-fold flyer design to match the amount of text. Inside is picture based manual (some basic fotoshopping of phone screenshot settings required). The outside is advertisement text with some pictures. (temporary created in MS publisher as reference included)
The result must be an A4 format tri-fold.
Text is provided, but needs to be editable afterwards for different languages.
Updates

There are updates for the text sections on the back:LinkHarbor in uw zaak?1. Wifi als advertentiemiddelGratis wifi is vanzelfsprekend.gebruik LinkHarbor WiFi om tegelijk slim uw zaak te promotenSocialConnect zorgt extra aandacht voor uw chatterbook pagina zodat uw klanten op de hoogte blijven. 2. BEREIK nieuwe klantenGemiddeld heeft een chatterbook gebruiker meer dan 200 vriendenElke bezoeker brengt uw zaak in de aandacht van hun sociaal netwerk.Geen enkel ander advertentiemedium bereikt zoveel potentiële klanten. 3. HELP MENSEN JE ZAAK TE VINDENHoe meer check-ins, hoe beter uw visibiliteit op FacebookUw zaak komt vaker voor in de zoekresultatenVia de Chatterbook App wordt uw zaak voorgesteld aan mensen die in de buurt zijn. De beste manier om uw zaak te promoten!ga naar www.linkharbor-example.be voor meer informatie. Added Thursday, November 24, 2016

Target Market(s)

bars, restaurants, fitness, shops,...

Industry/Entity Type

Printing

Font styles to use
Other font styles liked:
• Berlin Sans FB Demi

Colors
6b449b
a64599

Requirements
Must have
• Trifold need to be appealing, front page clear indication of 'Free Internet Inside' , the inside must have the 3 screenshots provided (needs polishing) or similar. It must be 3 clear steps.
• The back of the trifold is advertisement for our product.and try to get people to go-to our website.
• So the trifold is targetted to 2 type of customers;
• Our customers (Bar, Restautant, Shops owners,..) that need to implement our Chatterbok Wifi solution.
• And their customers to assist how they can use the free internet access, without the staff need to spend time to explain and assist them.
• A4 format!
Nice to have
• The message is this one: https://www.chatterbook-example.com/business/chatterbook-wifi
• The pictures from this site can be used

```html
<!DOCTYPE html>
<html lang="en">
<head>
<meta charset="utf-8">
<title>LinkHarbor WiFi – Trifold Inside</title>
<link href="https://fonts.googleapis.com/css2?family=Jost:wght@400;600;700&family=Inter:wght@400;500;600;700&display=swap" rel="stylesheet">
<style>
  :root{
    --violet:#6b449b;
    --magenta:#a64599;
    --deep-magenta:#8a1f8c;
    --head-text:#7a1f86;
    --head-strong:#3a1842;
    --page-bg:#dcdcdc;
    --panel-top:#d7d7da;
    --panel-light:#f3f3f4;
    --phone-body:#fbfbfb;
    --phone-edge:#cfcfd2;
    --ios-blue:#1a7cf5;
    --ios-green:#4cd964;
    --ios-line:#e2e2e6;
    --ios-grey:#8e8e93;
    --site-bar:#ececef;
    --ui-text:#1c1c1e;
  }
  *{box-sizing:border-box;margin:0;padding:0}
  html,body{width:1200px;height:800px;overflow:hidden}
  body{background:var(--page-bg);font-family:"Inter",Helvetica,Arial,sans-serif;position:relative}

  .trifold{position:absolute;left:60px;top:18px;width:1080px;height:764px;display:flex;box-shadow:0 6px 24px rgba(0,0,0,.18)}
  .panel{position:relative;width:360px;height:100%;background:linear-gradient(180deg,var(--panel-light) 0%,#ececee 100%);overflow:hidden}
  .panel + .panel{border-left:1px solid #e2e2e4}

  .panel-head{height:150px;border-top:5px solid var(--violet);background:linear-gradient(180deg,var(--panel-top) 0%,#e6e6e8 70%,var(--panel-light) 100%);display:flex;flex-direction:column;justify-content:center;align-items:center;gap:4px;font-family:"Jost",sans-serif;color:var(--head-text);font-size:19px;line-height:1.2}
  .panel-head strong{color:var(--head-strong);font-weight:700}

  .panel-foot{position:absolute;left:0;right:0;bottom:0;height:70px;border-top:4px solid #4a4a4f;background:linear-gradient(90deg,var(--deep-magenta) 0%,var(--magenta) 55%,var(--violet) 100%);display:flex;align-items:center;justify-content:center;gap:10px;color:#fff;font-family:"Jost",sans-serif;font-size:18px;letter-spacing:.3px}
  .globe{width:18px;height:18px}

  /* phone */
  .phone{position:absolute;left:65px;top:185px;width:230px;height:462px;border-radius:38px;background:var(--phone-body);border:2px solid var(--phone-edge);box-shadow:0 10px 26px rgba(0,0,0,.12),inset 0 0 0 5px #efeff1}
  .phone-camera{position:absolute;top:18px;left:74px;width:8px;height:8px;border-radius:50%;background:#2a2a2e}
  .phone-speaker{position:absolute;top:30px;left:90px;width:50px;height:5px;border-radius:3px;background:#3a3a3e}
  .phone-dot{position:absolute;top:14px;left:111px;width:6px;height:6px;border-radius:50%;background:#2a2a2e}
  .phone-home{position:absolute;bottom:14px;left:96px;width:38px;height:38px;border-radius:50%;border:2px solid #c7c7cb}
  .screen{position:absolute;top:56px;left:14px;width:198px;height:350px;background:#fff;border:1px solid #d3d3d6;overflow:hidden;font-size:9px;color:var(--ui-text)}

  .status-bar{height:14px;display:flex;justify-content:space-between;align-items:center;padding:0 6px;font-size:6.5px;font-weight:600;background:#f7f7f7}

  /* wifi screen */
  .nav-bar{height:22px;display:flex;align-items:center;padding:0 6px;background:#f7f7f7;border-bottom:1px solid var(--ios-line);position:relative}
  .nav-back{color:var(--ios-blue);font-size:8.5px}
  .nav-title{position:absolute;left:0;right:0;text-align:center;font-weight:600;font-size:9px;pointer-events:none}
  .settings-group{background:#fff;border-bottom:1px solid var(--ios-line)}
  .setting-row{height:21px;display:flex;align-items:center;padding:0 8px 0 18px;border-top:1px solid var(--ios-line);position:relative;font-size:8.5px}
  .setting-row:first-child{border-top:none}
  .setting-row .name{flex:1}
  .setting-row .sub{display:block;font-size:5.5px;color:var(--ios-grey)}
  .tick{position:absolute;left:6px;color:var(--ios-blue);font-size:8px}
  .toggle{width:24px;height:14px;border-radius:7px;background:var(--ios-green);position:relative}
  .toggle::after{content:"";position:absolute;right:1px;top:1px;width:12px;height:12px;border-radius:50%;background:#fff}
  .toggle.off{background:#e5e5ea}
  .toggle.off::after{left:1px;right:auto}
  .row-icons{display:flex;gap:4px;align-items:center;color:#333;font-size:7px}
  .info{width:10px;height:10px;border-radius:50%;border:1px solid var(--ios-blue);color:var(--ios-blue);font-size:7px;line-height:8px;text-align:center;font-weight:600}
  .group-label{background:#efeff4;padding:8px 8px 3px;font-size:6px;color:var(--ios-grey);letter-spacing:.3px}
  .group-note{background:#efeff4;padding:4px 8px;font-size:5.6px;color:var(--ios-grey);line-height:1.35}
  .spacer{height:10px;background:#efeff4}

  /* check-in screen */
  .url-bar{height:18px;background:#f7f7f7;display:flex;align-items:center;justify-content:center;font-size:7px;color:#333}
  .site-bar{height:22px;background:var(--site-bar);border-bottom:1px solid var(--ios-line);color:var(--ui-text);font-weight:500;font-size:9.5px;display:flex;align-items:center;justify-content:center}
  .cover-photo{height:92px;background:linear-gradient(135deg,#5a3a28 0%,#8b5a3a 45%,#c99a6e 75%,#3e2a1e 100%);position:relative}
  .page-profile{position:absolute;left:8px;bottom:-20px;width:50px;height:44px;background:#fff;border:2px solid #fff;box-shadow:0 1px 3px rgba(0,0,0,.3);display:flex;align-items:center;justify-content:center;font-family:"Jost",sans-serif;font-weight:600;font-size:8px;color:var(--magenta)}
  .page-name{padding:5px 0 0 64px;font-size:8.5px;font-weight:600;height:24px}
  .checkin{padding:8px 8px 4px;border-top:1px solid var(--ios-line)}
  .checkin h3{font-size:9.5px;font-weight:600;margin-bottom:6px}
  .checkin-actions{display:flex;align-items:center;gap:10px;margin-bottom:8px}
  .btn-checkin{background:var(--violet);color:#fff;font-size:6.5px;font-weight:600;padding:4px 7px;border-radius:2px}
  .status-add{font-size:6px;color:var(--ios-grey)}
  .skip-link{font-size:6px;color:var(--violet);text-decoration:underline;margin-bottom:3px}
  .legal{font-size:5.6px;color:var(--ios-grey);line-height:1.35}
  .toolbar{position:absolute;bottom:0;left:0;right:0;height:20px;background:#f7f7f7;border-top:1px solid var(--ios-line);display:flex;justify-content:space-around;align-items:center;color:var(--ios-blue);font-size:9px}

  /* access screen */
  .brand-word{margin:48px auto 0;text-align:center;font-family:"Jost",sans-serif;font-weight:700;font-size:26px;color:var(--magenta)}
  .apps-cluster{width:110px;height:92px;margin:18px auto 0;border-radius:14px;background:linear-gradient(135deg,#f2a33a 0%,#e4513f 35%,#3aa0d8 70%,#7b4fb0 100%);opacity:.85}
  .thumb-area{width:46px;height:48px;margin:18px auto 0;border-radius:8px;background:linear-gradient(180deg,#4aa3e8,#1c74c9)}
</style>
</head>
<body>
<main class="trifold">

  <!-- Step 1 -->
  <section class="panel">
    <header class="panel-head">
      <div>Choose Network <strong>LH_HarborCafe</strong></div>
      <div>Kies Netwerk <strong>LH_HarborCafe</strong></div>
    </header>
    <div class="phone">
      <span class="phone-dot"></span><span class="phone-camera"></span><span class="phone-speaker"></span>
      <div class="screen">
        <div class="status-bar"><span>●●●○○ Telora</span><span>14:19</span><span>78%</span></div>
        <div class="nav-bar"><span class="nav-back">‹ Settings</span><span class="nav-title">Wi-Fi</span></div>
        <div class="settings-group">
          <div class="setting-row"><span class="name">Wi-Fi</span><span class="toggle"></span></div>
          <div class="setting-row"><span class="tick">✓</span><span class="name">LH_HarborCafe<span class="sub">Security Recommendation</span></span><span class="row-icons">◠ <span class="info">i</span></span></div>
        </div>
        <div class="group-label">CHOOSE A NETWORK...</div>
        <div class="settings-group">
          <div class="setting-row"><span class="name">Cafe Secure</span><span class="row-icons">🔒 ◠ <span class="info">i</span></span></div>
          <div class="setting-row"><span class="name">KelvaroBoven</span><span class="row-icons">🔒 ◠ <span class="info">i</span></span></div>
          <div class="setting-row"><span class="name">KelvaroRange</span><span class="row-icons">🔒 ◠ <span class="info">i</span></span></div>
          <div class="setting-row"><span class="name">KelvaroSpeed</span><span class="row-icons">🔒 ◠ <span class="info">i</span></span></div>
          <div class="setting-row"><span class="name">Other...</span></div>
        </div>
        <div class="spacer"></div>
        <div class="settings-group">
          <div class="setting-row"><span class="name">Ask to Join Networks</span><span class="toggle off"></span></div>
        </div>
        <div class="group-note">Known networks will be joined automatically. If no known networks are available, you will have to manually select a network.</div>
      </div>
      <span class="phone-home"></span>
    </div>
    <footer class="panel-foot">
      <svg class="globe" viewBox="0 0 20 20" fill="none" stroke="#fff" stroke-width="1.5"><circle cx="10" cy="10" r="8"/><ellipse cx="10" cy="10" rx="3.5" ry="8"/><path d="M2 10h16M3.5 6h13M3.5 14h13"/></svg>
      <span>www.linkharbor-example.be</span>
    </footer>
  </section>

  <!-- Step 2 -->
  <section class="panel">
    <header class="panel-head">
      <div>CheckIn on <strong>Chatterbook</strong></div>
      <div>Inchecken op <strong>Chatterbook</strong></div>
    </header>
    <div class="phone">
      <span class="phone-dot"></span><span class="phone-camera"></span><span class="phone-speaker"></span>
      <div class="screen">
        <div class="status-bar"><span>●●●○○ Telora</span><span>14:20</span><span>78%</span></div>
        <div class="url-bar">🔒 chatterbook.com</div>
        <div class="site-bar">Chatterbook</div>
        <div class="cover-photo" role="img" aria-label="Cover photo of coffee cups on a café table">
          <div class="page-profile">LinkHarbor</div>
        </div>
        <div class="page-name">LH Café</div>
        <div class="checkin">
          <h3>Check in voor gratis internet</h3>
          <div class="checkin-actions"><span class="btn-checkin">Inchecken</span><span class="status-add">Status toevoegen</span></div>
          <div class="skip-link">Check-in overslaan</div>
          <p class="legal">Door Chatterbook Wi-Fi te gebruiken, geef je aan dat je akkoord gaat met de Wi-Fi-voorwaarden van Chatterbook.</p>
        </div>
        <div class="toolbar"><span>‹</span><span>›</span><span>⇪</span><span>▭</span><span>❐</span></div>
      </div>
      <span class="phone-home"></span>
    </div>
    <footer class="panel-foot">
      <svg class="globe" viewBox="0 0 20 20" fill="none" stroke="#fff" stroke-width="1.5"><circle cx="10" cy="10" r="8"/><ellipse cx="10" cy="10" rx="3.5" ry="8"/><path d="M2 10h16M3.5 6h13M3.5 14h13"/></svg>
      <span>www.linkharbor-example.be</span>
    </footer>
  </section>

  <!-- Step 3 -->
  <section class="panel">
    <header class="panel-head">
      <div><strong>Full Internet Access</strong></div>
      <div>Volledige Internet Toegang</div>
    </header>
    <div class="phone">
      <span class="phone-dot"></span><span class="phone-camera"></span><span class="phone-speaker"></span>
      <div class="screen">
        <div class="status-bar"><span>●●●○○ Telora</span><span>14:20</span><span>78%</span></div>
        <div class="brand-word">LinkHarbor</div>
        <div class="apps-cluster" role="img" aria-label="Cluster of colourful app icons"></div>
        <div class="thumb-area" role="img" aria-label="Blue thumbs-up illustration"></div>
      </div>
      <span class="phone-home"></span>
    </div>
    <footer class="panel-foot">
      <svg class="globe" viewBox="0 0 20 20" fill="none" stroke="#fff" stroke-width="1.5"><circle cx="10" cy="10" r="8"/><ellipse cx="10" cy="10" rx="3.5" ry="8"/><path d="M2 10h16M3.5 6h13M3.5 14h13"/></svg>
      <span>www.linkharbor-example.be</span>
    </footer>
  </section>

</main>
</body>
</html>
```